A NEW UPDATED VERSION OF A 4"X9" RACK CARD

A NEW UPDATED VERSION OF A RACK CARD, THIS CARD IS 5 YEARS OLD AND WE WANT SOMETHING NEW AND FRESH AND MORE UPDATED TO TODAY. MARKET TO A YOUNGER CROWD. USE THE ATTACHED RACK CARD FOR THE INFO AND VERBAGE AND LOGO TO BE USED. DO NOT USE THE PICTURE OF THE BUILDIING, don't use the picture of the 2 guys. USED THE ATTACHED POST CARDS AS COLORS AND REFERENCE.

Target Market(s)

25-45

Industry/Entity Type

HOME INSPECTIONS

```html
<!DOCTYPE html>
<html lang="en">
<head>
<meta charset="UTF-8">
<title>Keystone Home Inspection – Rack Card</title>
<link href="https://fonts.googleapis.com/css2?family=Oswald:wght@500;700&family=Montserrat:wght@400;600;800&display=swap" rel="stylesheet">
<style>
  :root{
    --navy:#1b3576;
    --navy-deep:#142a60;
    --red:#e1334b;
    --paper:#ebebed;
    --white:#ffffff;
    --stage:#efeeee;
    --photo-warm-a:#c9a57a;
    --photo-warm-b:#4a4238;
    --photo-snow-a:#f4f4f6;
    --photo-snow-b:#b88a4f;
  }
  *{box-sizing:border-box;margin:0;padding:0}
  html,body{width:1200px;height:900px;overflow:hidden}
  body{background:var(--stage);font-family:"Montserrat",sans-serif;position:relative}

  .rack-card{position:absolute;top:45px;width:360px;height:810px;overflow:hidden;background:var(--paper);box-shadow:0 6px 18px rgba(0,0,0,.12)}
  .rack-card--front{left:180px}
  .rack-card--back{left:660px}
  .card-art{position:absolute;inset:0}

  .rank-badge{position:absolute;left:24px;top:68px;width:54px;height:54px;border-radius:50%;border:3px solid var(--white);background:var(--navy);box-shadow:0 0 0 3px var(--red);color:var(--white);font:700 20px "Oswald",sans-serif;display:flex;align-items:center;justify-content:center}

  .brand-name{position:absolute;color:var(--navy);font:800 15px/1.15 "Montserrat",sans-serif;letter-spacing:1px;text-align:center;text-transform:uppercase;display:flex;align-items:center;justify-content:center;gap:8px}
  .brand-name .brand-dot{width:12px;height:12px;border-radius:50%;background:currentColor;flex:none}
  .brand-name--light{color:var(--white)}
  .front-brand{left:14px;top:330px;width:190px;font-size:14px}
  .front-footer-brand{left:40px;top:745px;width:280px}
  .back-brand{left:40px;top:690px;width:280px}

  .state-title{position:absolute;left:224px;top:322px;width:130px;color:var(--white);font:800 20px/1 "Montserrat",sans-serif;letter-spacing:.5px;white-space:nowrap}
  .state-sub{position:absolute;left:225px;top:348px;width:125px;color:var(--white);font:600 9px/1.2 "Montserrat",sans-serif;letter-spacing:.5px}

  .benefit-list{position:absolute;left:40px;top:460px;width:280px;list-style:none;text-align:center;color:var(--white)}
  .benefit-list li{font:400 12px/1.3 "Montserrat",sans-serif;letter-spacing:1px;margin-bottom:16px;text-transform:uppercase}

  .web-band{position:absolute;left:0;top:650px;width:360px;height:44px;background:var(--white);color:var(--navy);font:700 21px/44px "Oswald",sans-serif;text-align:center;letter-spacing:.5px}
  .call-band{position:absolute;left:0;top:694px;width:360px;height:40px;background:var(--red);color:var(--white);font:800 18px/40px "Montserrat",sans-serif;text-align:center;letter-spacing:1px}

  .why-title{position:absolute;left:0;top:0;width:360px;height:46px;color:var(--white);font:700 19px/46px "Oswald",sans-serif;text-align:center;letter-spacing:.3px;white-space:nowrap}

  .feature{position:absolute;display:flex;align-items:center;gap:8px;color:var(--white);font:400 10.5px/1.15 "Montserrat",sans-serif;letter-spacing:.6px;text-transform:uppercase}
  .feature svg{flex:none;width:28px;height:28px}
  .feature--left{left:16px}
  .feature--right{right:16px;text-align:right}
</style>
</head>
<body>

<article class="rack-card rack-card--front">
  <svg class="card-art" viewBox="0 0 360 810" width="360" height="810">
    <defs>
      <linearGradient id="streetGrad" x1="0" y1="0" x2="1" y2="1">
        <stop offset="0" stop-color="var(--photo-warm-a)"/>
        <stop offset="1" stop-color="var(--photo-warm-b)"/>
      </linearGradient>
      <linearGradient id="flagGlow" x1="0" y1="0" x2="1" y2="0">
        <stop offset="0" stop-color="#3d59a0" stop-opacity=".55"/>
        <stop offset="1" stop-color="#7a6aa8" stop-opacity=".45"/>
      </linearGradient>
    </defs>
    <rect x="0" y="0" width="360" height="192" fill="var(--navy)"/>
    <polygon points="180,0 360,0 360,192 90,192" fill="url(#streetGrad)" role="img" aria-label="Photo of sunlit townhouses along a street"/>
    <rect x="0" y="192" width="360" height="240" fill="var(--paper)"/>
    <polygon points="230,192 360,192 360,432 216,432 216,300" fill="var(--red)"/>
    <polygon points="0,200 230,200 220,214 0,214" fill="var(--navy)"/>
    <polygon points="0,222 210,222 160,290 0,290" fill="var(--navy)"/>
    <polygon points="70,222 98,222 60,290 30,290" fill="var(--white)"/>
    <polygon points="145,222 162,222 118,290 100,290" fill="var(--white)"/>
    <rect x="0" y="432" width="360" height="378" fill="var(--navy)"/>
    <rect x="40" y="470" width="280" height="150" rx="40" fill="url(#flagGlow)" role="img" aria-label="Soft waving flag decoration"/>
  </svg>

  <div class="rank-badge">#1</div>

  <div class="brand-name front-brand"><span class="brand-dot"></span>Keystone Home Inspection</div>

  <div class="state-title">FLORIDA'S</div>
  <div class="state-sub">#1 INSPECTION COMPANY</div>

  <ul class="benefit-list">
    <li>Early detection of costly issues</li>
    <li>Maximize your warranty</li>
    <li>Plan future repairs</li>
    <li>Ensure a safe and livable home</li>
    <li>Expert advice on repairs</li>
  </ul>

  <div class="web-band">WWW.KEYSTONEHOMEINSPECT.COM</div>
  <div class="call-band">CALL US 1-800-555-0142</div>

  <div class="brand-name brand-name--light front-footer-brand"><span class="brand-dot"></span>Keystone Home Inspection</div>
</article>

<article class="rack-card rack-card--back">
  <svg class="card-art" viewBox="0 0 360 810" width="360" height="810">
    <defs>
      <linearGradient id="snowGrad" x1="0" y1="0" x2="0" y2="1">
        <stop offset="0" stop-color="var(--photo-snow-a)"/>
        <stop offset=".55" stop-color="var(--photo-snow-b)"/>
        <stop offset="1" stop-color="var(--photo-snow-a)"/>
      </linearGradient>
    </defs>
    <rect x="0" y="0" width="360" height="810" fill="var(--paper)"/>
    <rect x="0" y="300" width="360" height="320" fill="url(#snowGrad)" role="img" aria-label="Photo of a brick house with a turret in winter snow"/>
    <rect x="0" y="0" width="360" height="46" fill="var(--navy)"/>
    <polygon points="0,46 360,46 360,270 180,400 0,290" fill="var(--red)"/>
    <rect x="0" y="618" width="360" height="192" fill="var(--navy)"/>
  </svg>

  <h2 class="why-title">WHY CHOOSE KEYSTONE HOME INSPECTION?</h2>

  <div class="feature feature--left" style="top:80px">
    <svg viewBox="0 0 28 28" fill="none" stroke="#fff" stroke-width="2"><path d="M14 3 L24 7 V14 C24 20 19 24 14 26 C9 24 4 20 4 14 V7 Z"/><path d="M9 14 L13 18 L19 10"/></svg>
    <span class="feature-text">Trusted industry<br>professional with<br>over 20 yrs of<br>experience</span>
  </div>
  <div class="feature feature--left" style="top:150px">
    <svg viewBox="0 0 28 28" fill="none" stroke="#fff" stroke-width="2.4"><circle cx="16" cy="11" r="7"/><path d="M11 16 L4 24"/></svg>
    <span class="feature-text">Thorough<br>comprehensive<br>inspection</span>
  </div>
  <div class="feature feature--left" style="top:212px">
    <svg viewBox="0 0 28 28" fill="none" stroke="#fff" stroke-width="2"><path d="M4 13 C4 7 9 4 14 4 C19 4 24 7 24 13 C24 19 19 21 14 21 L8 24 L9 20 C6 19 4 16 4 13 Z"/><circle cx="10" cy="13" r="1" fill="#fff"/><circle cx="14" cy="13" r="1" fill="#fff"/><circle cx="18" cy="13" r="1" fill="#fff"/></svg>
    <span class="feature-text">Excellent<br>customer<br>service &amp;<br>support</span>
  </div>

  <div class="feature feature--right" style="top:70px">
    <span class="feature-text">Certified &amp;<br>licensed<br>inspectors</span>
    <svg viewBox="0 0 28 28" fill="none" stroke="#fff" stroke-width="2"><rect x="3" y="5" width="20" height="15" rx="1"/><path d="M7 10 H18 M7 14 H13"/><circle cx="20" cy="19" r="3.5"/><path d="M18 22 L17 26 M22 22 L23 26"/></svg>
  </div>
  <div class="feature feature--right" style="top:132px">
    <span class="feature-text">Competitive<br>pricing and<br>value</span>
    <svg viewBox="0 0 28 28" fill="none" stroke="#fff" stroke-width="2"><path d="M5 8 L13 4 H22 V24 H13 L5 20 Z"/><path d="M17 9 C15 9 13 10 13 12 C13 15 19 14 19 17 C19 19 17 20 15 20 M16 7 V22"/></svg>
  </div>
  <div class="feature feature--right" style="top:195px">
    <span class="feature-text">Detailed<br>inspection<br>report with<br>photos</span>
    <svg viewBox="0 0 28 28" fill="none" stroke="#fff" stroke-width="2"><rect x="5" y="3" width="18" height="22" rx="1"/><rect x="8" y="7" width="5" height="4"/><path d="M15 8 H20 M8 15 H20 M8 19 H20"/></svg>
  </div>

  <div class="brand-name brand-name--light back-brand"><span class="brand-dot"></span>Keystone Home Inspection</div>
</article>

</body>
</html>
```